Home Loan Introducer needs logo/business cards

We need a simple but classy logo for business cards and flyers. The business is a home loan referral business that is called an Introducer. The business name is "The Harborline".
I was thinking very simple and straight to the point on the front with "Home Loans" the only thing on the front with a nice background colour/s.
Then on the back, "The Harborline"
and "Quality Customer Service"
and "Email, text or call welcome"
and then my name, email address and phone number.
Updates
Thank you for all the designs :-)
Target Market(s)
Home buyers.
Home owners.
Investors.
Industry/Entity Type
Loan
Look and feel

```html
<!DOCTYPE html>
<html lang="en">
<head>
<meta charset="utf-8">
<title>The Harborline – Business Cards</title>
<link rel="stylesheet" href="https://fonts.googleapis.com/css2?family=Exo+2:wght@600;700&family=Abel&family=Open+Sans:ital,wght@1,300&display=swap">
<style>
  :root {
    --canvas-grey: #c8c8c8;
    --brand-blue: #0066b2;
    --brand-orange: #fbab33;
    --orange-light: #fdd08a;
    --paper: #ffffff;
  }
  * { margin: 0; padding: 0; box-sizing: border-box; }
  html, body {
    width: 1160px; height: 1200px; overflow: hidden;
    background: var(--canvas-grey);
  }
  .canvas { position: relative; width: 1160px; height: 1200px; }

  .card {
    position: absolute; left: 129px; width: 867px; height: 528px;
    overflow: hidden;
    box-shadow: 4px 5px 8px rgba(0,0,0,0.45);
  }

  /* Front */
  .card-front { top: 47px; background: var(--brand-blue); }
  .front-strip {
    position: absolute; left: 0; right: 0; top: 182px; height: 160px;
    background: var(--paper);
  }
  .front-band {
    position: absolute; left: 0; right: 3px; top: 190px; height: 146px;
    background: var(--brand-orange); border-radius: 0 10px 10px 0;
    display: flex; align-items: center; justify-content: center;
  }
  .front-title {
    font-family: "Exo 2", sans-serif; font-weight: 700;
    font-size: 112px; letter-spacing: 2px; line-height: 1;
    color: var(--paper); margin-top: 14px;
  }

  /* Back */
  .card-back { top: 613px; background: var(--paper); }
  .back-panel {
    position: absolute; left: 480px; top: 0; right: 0; bottom: 0;
    background: var(--brand-orange);
  }
  .back-panel-decor {
    position: absolute; inset: 0;
    background: radial-gradient(ellipse at 85% 35%, rgba(255,236,200,0.75) 0%, rgba(253,208,138,0.4) 35%, rgba(251,171,51,0) 70%);
  }
  .back-rule {
    position: absolute; left: 0; right: 0; height: 27px;
    background: var(--brand-blue);
  }
  .back-rule--top { top: 80px; }
  .back-rule--bottom { top: 398px; }

  .brand-mark {
    position: absolute; left: 48px; top: 162px; width: 392px;
    display: flex; flex-direction: column; align-items: center;
  }
  .brand-mark svg { display: block; margin-bottom: 22px; }
  .brand-name {
    width: 392px; height: 51px; border-radius: 6px;
    background: var(--brand-orange);
    display: flex; align-items: center; justify-content: center;
    font-family: "Exo 2", sans-serif; font-weight: 700;
    font-size: 36px; color: var(--paper); letter-spacing: 0.5px;
  }

  .contact {
    position: absolute; left: 498px; top: 160px; width: 340px;
    color: var(--paper);
  }
  .contact-tagline {
    font-family: "Abel", sans-serif; font-size: 23px; line-height: 27px;
  }
  .contact-company {
    font-family: "Abel", sans-serif; font-size: 30px; color: var(--brand-blue);
    margin-top: 10px; padding-bottom: 6px; width: 300px;
    border-bottom: 3px dotted var(--brand-blue);
  }
  .contact-name {
    font-family: "Open Sans", sans-serif; font-style: italic; font-weight: 300;
    font-size: 26px; margin-top: 6px; line-height: 32px;
  }
  .contact-detail {
    font-family: "Abel", sans-serif; font-size: 21px; line-height: 27px;
    padding-left: 4px;
  }
</style>
</head>
<body>
<main class="canvas">

  <section class="card card-front" aria-label="Business card front">
    <div class="front-strip"></div>
    <div class="front-band">
      <h1 class="front-title">HOME LOAN</h1>
    </div>
  </section>

  <section class="card card-back" aria-label="Business card back">
    <div class="back-panel">
      <div class="back-panel-decor" role="img" aria-label="Faint soft-lit house decoration in light orange tones"></div>
    </div>
    <div class="back-rule back-rule--top"></div>
    <div class="back-rule back-rule--bottom"></div>

    <div class="brand-mark">
      <svg width="132" height="132" viewBox="0 0 132 132" aria-hidden="true">
        <circle cx="66" cy="66" r="64" fill="var(--brand-blue)"/>
      </svg>
      <div class="brand-name">THE HARBORLINE</div>
    </div>

    <div class="contact">
      <p class="contact-tagline">Quality Customer Service</p>
      <p class="contact-tagline">Email, text or call are Welcome</p>
      <p class="contact-company">The Harborline</p>
      <p class="contact-name">Daniel Moreno</p>
      <p class="contact-detail">theharborline@mailbox.example</p>
      <p class="contact-detail">+639517724086</p>
    </div>
  </section>

</main>
</body>
</html>
```